Business card for a Exhibition booth fabrication company

Hi. My company would like to change our corporate name card. We are an events and Exhibition stand builder company. We would like our corporate name card to resonate what we do. I need someone to create something unique that relates to the industry that I am in. The graphic designer should be creative to incorporate the elements of my industry and try to blend in well in the design of the card. Our aim is to ensure that we are unique and our card can look different from our competitors.
Updates

Target Market(s)

Marketing and events manager from all companies

Contact Information for Business Card

The business card should have the following details:
Name
Job Title
Email
Website

Colors

Designer to choose colors to be used in the design.

Requirements
Must have
• The card must be look something that is relevant to the service that I am providing. My website is: www.velmora-buildworks.com
• You can see my website to get more information on what service that I am doing
Nice to have
• On the back of my card, I would like to have a globe image with the incorporation of my company logo. This is to indicate that my services can be done in any part of the world.

```html
<!DOCTYPE html>
<html lang="en">
<head>
<meta charset="utf-8">
<title>Velmora Buildworks – Business Card</title>
<link rel="stylesheet" href="https://fonts.googleapis.com/css2?family=Michroma&family=Open+Sans:wght@400;600&display=swap">
<style>
  :root {
    --bg: #3a3a3c;
    --red: #ed1c24;
    --red-deep: #7e0d12;
    --red-mid: #b5151b;
    --white: #ffffff;
    --map-blue: #e1f1f8;
    --brand-grey: #6b6b6b;
  }
  * { box-sizing: border-box; margin: 0; padding: 0; }
  html, body { width: 1200px; height: 896px; overflow: hidden; }
  body {
    background: var(--bg);
    display: flex;
    align-items: center;
    justify-content: center;
    gap: 40px;
  }
  .card {
    position: relative;
    width: 540px;
    height: 309px;
    overflow: hidden;
    background: var(--white);
    box-shadow: 0 10px 24px rgba(0,0,0,.35);
  }

  /* Front */
  .card-front .red-panel {
    position: absolute;
    inset: 0;
    width: 100%;
    height: 100%;
  }
  .card-front .brand {
    position: absolute;
    left: 34px;
    top: 34px;
    font-family: "Michroma", sans-serif;
    font-size: 21px;
    letter-spacing: 3px;
    color: var(--white);
  }
  .card-front .person {
    position: absolute;
    left: 34px;
    top: 120px;
    color: var(--white);
  }
  .person-name {
    font-family: "Michroma", sans-serif;
    font-size: 17px;
    letter-spacing: 1px;
    line-height: 1;
  }
  .person-title {
    font-family: "Open Sans", sans-serif;
    font-size: 13px;
    margin-top: 3px;
  }
  .contact-list {
    list-style: none;
    margin-top: 12px;
    font-family: "Open Sans", sans-serif;
    font-size: 12.5px;
    line-height: 1.45;
  }
  .contact-list li { display: flex; align-items: center; gap: 7px; }
  .contact-list svg { width: 13px; height: 13px; flex: none; }

  /* Back */
  .card-back .world-map {
    position: absolute;
    left: 0; top: 0;
    width: 100%; height: 100%;
  }
  .card-back .brand-mark {
    position: absolute;
    left: 50%;
    top: 50%;
    transform: translate(-50%, -50%);
    display: flex;
    align-items: center;
    gap: 12px;
    white-space: nowrap;
  }
  .brand-dot {
    width: 22px; height: 22px;
    border-radius: 50%;
    background: var(--red);
  }
  .brand-name {
    font-family: "Michroma", sans-serif;
    font-size: 22px;
    letter-spacing: 3px;
    color: var(--brand-grey);
  }
</style>
</head>
<body>

  <section class="card card-front" aria-label="Business card front">
    <svg class="red-panel" viewBox="0 0 540 309" preserveAspectRatio="none" aria-hidden="true">
      <defs>
        <linearGradient id="panelFill" x1="1" y1="0" x2="0" y2="1">
          <stop offset="0" stop-color="var(--red-deep)"/>
          <stop offset="0.55" stop-color="var(--red-mid)"/>
          <stop offset="1" stop-color="var(--red)"/>
        </linearGradient>
      </defs>
      <polygon points="0,0 540,0 540,118 0,309" fill="url(#panelFill)"/>
      <polygon points="540,118 540,168 120,309 0,309" fill="var(--red)"/>
    </svg>
    <div class="brand">VELMORA BUILDWORKS</div>
    <div class="person">
      <div class="person-name">DANIEL HARKER</div>
      <div class="person-title">Managing Director</div>
      <ul class="contact-list">
        <li>
          <svg viewBox="0 0 16 16"><path fill="#fff" d="M2 5c0-2 2-3 6-3s6 1 6 3v1h-3V5H5v1H2zM4 7h8l2 7H2z"/></svg>
          +65 81472036 (Singapore)
        </li>
        <li>
          <svg viewBox="0 0 16 16"><path fill="#fff" d="M2 5c0-2 2-3 6-3s6 1 6 3v1h-3V5H5v1H2zM4 7h8l2 7H2z"/></svg>
          +974 55128470 (Qatar)
        </li>
        <li>
          <svg viewBox="0 0 16 16"><rect x="1" y="3" width="14" height="10" fill="#fff"/><path d="M1 3l7 6 7-6" fill="none" stroke="#b5151b" stroke-width="1.4"/></svg>
          info@velmora-buildworks.com
        </li>
        <li>
          <svg viewBox="0 0 16 16"><circle cx="8" cy="8" r="7" fill="#fff"/><path d="M1 8h14M8 1c-3 3-3 11 0 14M8 1c3 3 3 11 0 14" fill="none" stroke="#b5151b" stroke-width="1.1"/></svg>
          www.velmora-buildworks.com
        </li>
      </ul>
    </div>
  </section>

  <section class="card card-back" aria-label="Business card back">
    <svg class="world-map" viewBox="0 0 540 309" role="img" aria-label="Faint light-blue world map across the card">
      <rect width="540" height="309" fill="var(--map-blue)" opacity="0.55"/>
    </svg>
    <div class="brand-mark">
      <span class="brand-dot"></span>
      <span class="brand-name">VELMORA BUILDWORKS</span>
    </div>
  </section>

</body>
</html>
```